Website for new dental office

I am Dr. Colin Ashford and am building a new dental practice. I specialize in general dentistry. I am young and have a higher end dental practice incorporating very new technologies and would like my website to reflect that. As many dental patients are older, the website must be very easy to navigate. I would like patients to be able to request appointments, and will eventually add on patient information forms (the health history, etc, that you normally fill out in the practice) from my practice management software, so leave an area for that.

Industry/Entity Type

Building

```html
<!DOCTYPE html>
<html lang="en">
<head>
<meta charset="utf-8">
<title>Colin Ashford, DDS</title>
<link rel="stylesheet" href="https://fonts.googleapis.com/css2?family=Open+Sans:wght@400;600&family=PT+Serif:wght@700&family=Bitter:wght@500&display=swap">
<style>
:root{
  --blue:#4a69ad;
  --blue-dark:#22386e;
  --green:#8bd12a;
  --orange:#f59a16;
  --orange-light:#fbb33a;
  --panel:#2d2d2d;
  --footer:#262626;
  --footer-bottom:#1b1b1b;
  --text:#555;
  --muted:#888;
  --line:#d9d9d9;
}
*{box-sizing:border-box;margin:0;padding:0}
html,body{width:890px;height:1200px;overflow:hidden}
body{position:relative;background:#fff;font-family:"Open Sans",sans-serif;color:var(--text)}

.site-header{position:absolute;left:0;top:0;width:890px;height:101px;background:linear-gradient(#4f6db0,#6382c2)}
.brand{position:absolute;left:82px;top:22px;font-family:"PT Serif",serif;font-weight:700;color:#fff;line-height:1}
.brand .l1{font-size:34px;letter-spacing:1px}
.brand .l2{font-size:25px;margin-top:2px}
.call{position:absolute;left:475px;top:25px;color:#fff;font-size:16px}
.consult{position:absolute;left:638px;top:20px;width:170px;height:30px;background:var(--green);border:1px solid #a6e24a;border-radius:3px;color:#fff;font-family:"Bitter",serif;font-size:15px;line-height:28px;padding-left:10px;white-space:nowrap}
.consult svg{position:absolute;right:7px;top:5px}
.main-nav{position:absolute;left:332px;top:64px;width:476px;height:37px;background:linear-gradient(#fff,#e9e9e9);border-radius:3px 3px 0 0;display:flex;justify-content:space-between;font-size:11.5px;color:#444;padding-right:14px}
.main-nav a{display:block;line-height:37px;text-decoration:none;color:inherit;white-space:nowrap}
.main-nav a.active{background:var(--blue-dark);color:#fff;width:73px;text-align:center;border-radius:3px 0 0 0}

.page{position:absolute;left:81px;top:101px;width:727px;height:857px;background:#fff;box-shadow:0 0 24px rgba(0,0,0,.18)}

.hero{position:absolute;left:89px;top:109px;width:709px;height:297px;box-shadow:0 10px 18px rgba(0,0,0,.15)}
.hero-photo{position:absolute;left:215px;top:0;width:494px;height:297px;background:linear-gradient(90deg,#eef2f5 0%,#e4e9ee 45%,#d9c2ac 70%,#f1f3f6 100%)}
.appt{position:absolute;left:0;top:0;width:215px;height:297px;background:var(--panel);border-left:7px solid #222;padding:14px 0 0 0;color:#fff}
.appt h2{font-weight:400;font-size:16px;margin-left:10px;white-space:nowrap}
.appt p{font-size:9.5px;line-height:12px;margin:4px 8px 0 11px;color:#eee}
.field{margin-top:10px;height:28px;background:#fff;border-radius:2px;border:1px solid #ccc;color:#aaa;font-size:9px;line-height:26px;padding-left:7px;width:200px;position:relative}
.field:first-of-type{margin-top:17px}
.field .caret{position:absolute;right:6px;top:0;font-size:8px}
.submit{margin-top:17px;width:95px;height:30px;background:linear-gradient(var(--orange-light),var(--orange));color:#fff;font-size:14px;font-weight:600;text-align:center;line-height:30px;border-radius:2px}

.tabs{position:absolute;left:83px;top:453px;display:flex;height:39px;border:1px solid var(--line);border-bottom:none;background:#fff}
.tabs div{line-height:39px;font-size:13.5px;color:#444;border-left:1px solid var(--line);text-align:center;white-space:nowrap}
.tabs div.active{background:var(--blue-dark);color:#fff;border:none}
.tab-panel{position:absolute;left:83px;top:492px;width:720px;height:159px;background:#f7f5f5;border:1px solid var(--line);border-radius:0 0 3px 3px}
.team-photo{position:absolute;left:8px;top:10px;width:234px;height:139px;background:linear-gradient(90deg,#c9dbe9,#e9eef2 50%,#c5d6e3)}
.tab-text{position:absolute;left:253px;top:27px;width:450px;font-size:9px;line-height:13.4px;color:var(--muted)}
.btn-grey{position:absolute;left:257px;top:121px;width:79px;height:25px;background:linear-gradient(#6c6c6c,#4f4f4f);color:#fff;font-size:10.5px;line-height:25px;text-align:center;border-radius:3px}

.sec-title{position:absolute;top:683px;font-size:17px;font-weight:400;color:#333;display:flex;align-items:center;white-space:nowrap}
.sec-title .rule{height:2px;background:var(--blue);margin-left:6px;flex:none}
.sec-title .dots{border-top:1px dotted #aaa;flex:1}
.case-intro{position:absolute;left:88px;top:712px;width:432px;font-size:9.5px;line-height:15px;color:var(--muted)}
.checks{position:absolute;left:86px;top:770px;list-style:none}
.checks li{display:flex;align-items:center;height:26.8px;font-size:11px;color:#555;white-space:nowrap}
.checks svg{margin-right:8px}
.btn-orange{position:absolute;left:85px;top:916px;width:79px;height:24px;background:linear-gradient(var(--orange-light),var(--orange));color:#fff;font-size:10.5px;line-height:24px;text-align:center}

.testi-photo{position:absolute;left:564px;top:712px;width:233px;height:133px;border:1px solid #ddd;background:radial-gradient(ellipse at 50% 40%,#d9a07f 0%,#e6c1a7 35%,#f6f1ee 70%)}
.quote-badge{position:absolute;left:660px;top:826px}
.quote{position:absolute;left:580px;top:866px;width:200px;text-align:center;font-size:12px;line-height:18.5px;color:#444}
.author{position:absolute;left:580px;top:928px;width:200px;text-align:center;font-size:8.5px;color:var(--muted)}
.author span{color:var(--blue)}

.site-footer{position:absolute;left:0;top:957px;width:890px;height:211px;background:var(--footer);color:#ddd}
.foot-brand{position:absolute;left:82px;top:32px;font-family:"PT Serif",serif;font-weight:700;font-size:22px;color:#fff;white-space:nowrap}
.foot-about{position:absolute;left:85px;top:76px;width:205px;font-size:9.5px;line-height:13.4px;color:#ddd}
.social{position:absolute;left:86px;top:159px;display:flex;gap:4.6px}
.social span{width:17px;height:17px;border-radius:50%;background:#555}
.foot-col{position:absolute;top:25px}
.foot-col h3{font-weight:400;font-size:14px;color:#fff}
.foot-links{list-style:none;margin-top:14px;font-size:9.5px;line-height:13.4px}
.contact-line{display:flex;align-items:center;gap:6px;font-size:9.5px;margin-top:6px;white-space:nowrap}
.contact-line:first-of-type{margin-top:14px}
.map{position:absolute;left:637px;top:55px;width:169px;height:123px;background:linear-gradient(135deg,#e6e3da,#f2efe6 50%,#ddd9cc);border:2px solid #fff}
.foot-bottom{position:absolute;left:0;top:1168px;width:890px;height:32px;background:var(--footer-bottom);color:#eee;font-size:9.5px;text-align:center;line-height:32px}
</style>
</head>
<body>

<header class="site-header">
  <div class="brand"><div class="l1">COLIN</div><div class="l2">Ashford, DDS</div></div>
  <div class="call">Call: +1 555 014 2290</div>
  <div class="consult">Free Consultancy
    <svg width="20" height="20" viewBox="0 0 20 20"><circle cx="8" cy="8" r="7" fill="#fff"/><circle cx="14" cy="13" r="5" fill="#fff" stroke="var(--green)" stroke-width="1.5"/><circle cx="5" cy="8" r="1" fill="var(--green)"/><circle cx="8" cy="8" r="1" fill="var(--green)"/><circle cx="11" cy="8" r="1" fill="var(--green)"/></svg>
  </div>
  <nav class="main-nav">
    <a class="active">HOME</a><a>Our Team</a><a>Philosophy</a><a>Restorative</a><a>Cosmetic</a><a>Contact</a>
  </nav>
</header>

<div class="page"></div>

<section class="hero">
  <form class="appt">
    <h2>Request an Appointment</h2>
    <p>Lorem Ipsum is simply dummy text of the printing and typesetting industry.</p>
    <div class="field">Name</div>
    <div class="field">Phone</div>
    <div class="field">Email</div>
    <div class="field">Appointment Day<span class="caret">▼</span></div>
    <div class="submit">SUBMIT</div>
  </form>
  <div class="hero-photo" role="img" aria-label="Smiling young dentist in a white coat with a stethoscope in a bright clinic"></div>
</section>

<div class="tabs"><div class="active" style="width:98px">Our Team</div><div style="width:134px">Patients Stories</div><div style="width:126px">Health History</div></div>
<section class="tab-panel">
  <div class="team-photo" role="img" aria-label="Dental team in white coats standing together"></div>
  <p class="tab-text">Lorem Ipsum is simply dummy text of the printing and typesetting industry. Lorem Ipsum has been the industry's standard dummy text ever since the 1500s, when an unknown printer took a galley of type and scrambled it to make a type specimen book. It has survived not only five centuries, but also the leap into electronic typesetting, remaining essentially unchanged. It was popularised in the 1960s . Lorem Ipsum is simply dummy text of the printing and typesetting industry. Lorem Ipsum has been the industry's standard dummy text ever since the 1500s.</p>
  <div class="btn-grey">Read More</div>
</section>

<h2 class="sec-title" style="left:86px;width:431px">Case Studies <span class="rule" style="width:86px"></span><span class="dots"></span></h2>
<p class="case-intro">Lorem Ipsum is simply dummy text of the printing and typesetting industry. Lorem Ipsum has been the industry's standard dummy text ever since the 1500s, when an unknown printer took a galley of type and scrambled it to make a type specimen book.</p>
<ul class="checks">
  <li><svg width="21" height="21" viewBox="0 0 21 21"><circle cx="10.5" cy="10.5" r="10.5" fill="var(--blue)"/><path d="M6 11l3 3 6-7" stroke="#fff" stroke-width="2.2" fill="none"/></svg>Lorem ipsum dolor sit amet, consectetur adipisicing elit, sed do.</li>
  <li><svg width="21" height="21" viewBox="0 0 21 21"><circle cx="10.5" cy="10.5" r="10.5" fill="var(--blue)"/><path d="M6 11l3 3 6-7" stroke="#fff" stroke-width="2.2" fill="none"/></svg>Lorem ipsum dolor sit amet, consectetur adipisicing elit, sed do.</li>
  <li><svg width="21" height="21" viewBox="0 0 21 21"><circle cx="10.5" cy="10.5" r="10.5" fill="var(--blue)"/><path d="M6 11l3 3 6-7" stroke="#fff" stroke-width="2.2" fill="none"/></svg>Lorem ipsum dolor sit amet, consectetur adipisicing elit, sed do.</li>
  <li><svg width="21" height="21" viewBox="0 0 21 21"><circle cx="10.5" cy="10.5" r="10.5" fill="var(--blue)"/><path d="M6 11l3 3 6-7" stroke="#fff" stroke-width="2.2" fill="none"/></svg>Lorem ipsum dolor sit amet, consectetur adipisicing elit, sed do.</li>
  <li><svg width="21" height="21" viewBox="0 0 21 21"><circle cx="10.5" cy="10.5" r="10.5" fill="var(--blue)"/><path d="M6 11l3 3 6-7" stroke="#fff" stroke-width="2.2" fill="none"/></svg>Lorem ipsum dolor sit amet, consectetur adipisicing elit, sed do.</li>
</ul>
<div class="btn-orange">Read More</div>

<h2 class="sec-title" style="left:562px;width:246px">Testimonials <span class="rule" style="width:42px"></span><span class="dots"></span></h2>
<div class="testi-photo" role="img" aria-label="Smiling patient with bright white teeth"></div>
<svg class="quote-badge" width="38" height="38" viewBox="0 0 38 38"><circle cx="19" cy="19" r="19" fill="var(--blue)"/><path d="M11 24v-5c0-3 2-5 4-6v2c-1 1-2 2-2 3h2v6zM21 24v-5c0-3 2-5 4-6v2c-1 1-2 2-2 3h2v6z" fill="#fff"/></svg>
<p class="quote">„ Praesent vestibulum molestie lacus. Aenean nonummy. Hendrerit mauris phasellus.”</p>
<p class="author">Nora Pell, <span>29 years</span></p>

<footer class="site-footer">
  <div class="foot-brand">Colin Ashford, DDS</div>
  <p class="foot-about">Lorem ipsum dolor sit amet, consectetur adipisicing elit, sed do eiusmod tempor incididunt ut labore et dolore magna aliqua. Ut enim ad minim veniam, quis nostrud exercitation.</p>
  <div class="social"><span></span><span></span><span></span><span></span><span></span><span></span><span></span></div>
  <div class="foot-col" style="left:330px"><h3>Navigation</h3>
    <ul class="foot-links"><li>Home</li><li>Our Team</li><li>Philosophy</li><li>Restorative</li><li>Cosmetic</li><li>Tooth Replacement</li><li>First Visit Contact</li></ul>
  </div>
  <div class="foot-col" style="left:465px"><h3>Contact Us</h3>
    <div class="contact-line"><svg width="10" height="10" viewBox="0 0 10 10"><path d="M2 1l2 2-1 1c0 1 2 3 3 3l1-1 2 2-1 2C4 10 0 6 0 2z" fill="#ddd"/></svg>Phone : +1 555 014 7789</div>
    <div class="contact-line"><svg width="11" height="8" viewBox="0 0 11 8"><rect width="11" height="8" fill="#ddd"/><path d="M0 0l5.5 4.5L11 0" stroke="#262626" fill="none"/></svg>Email : info@colinashford.com</div>
  </div>
  <div class="foot-col" style="left:637px"><h3>Find Us</h3></div>
  <div class="map" role="img" aria-label="Street map showing the office location"></div>
</footer>
<div class="foot-bottom">Copyright © 2014 Colin Ashford . All Rights Reserved.</div>

</body>
</html>
```